Small B&W Ear Panel Spa Newspaper Ad

We need a redesign for our Daily Ear Panel Newspaper Advertisement which appears in Coral Herald daily newspaper in Dubai.
The advert is small, size 40mm x 25mm, and it is in B&W, or black, grey and white.
The advert is for Lotusvale Spa and Massage Centres.
We attach the current pdf file which we use - the information included in the current ad is :
lotusvale
Balinese Massage Centres
Spa
800 PIMBELO
British Owned & Managed
www.lotusvale.ae
The advert is very small, and the MINIMUM information we would like to include is :
lotusvale
Spa
800 PIMBELO
ww.lotusvale.ae
It is optional to include the extra information :
Balinese Massage Centres
British Owned & Managed
The main brief is that the Advert must be BOLD & EYE-CATCHING.
iT MAY BE BEST TO KEEP THE ADVERT SIMPLE IN ORDER TO ACHIEVE THIS.
We like the current "rounded" edges to the box.
It may be best to use shades of black, grey and white.
We attach also 2 pictures of the front page of the Newspaper so that you can see how the Ad sits on the page, and how small it is.
The advert appears every day, so it must also be memorable, so that readers become used to it, whilst it still attracts their attention.
ONE POSSIBLE IDEA - PERHAPS THE ADVERT CAN BE A CIRCULAR, ROUND OR OVAL DESIGN, WHICH WOULD GIVE MORE BLANK WHITE SPACE AROUND IT, SO THAT IT WOULD STAND OUT MORE.

```html
<!DOCTYPE html>
<html lang="en">
<head>
<meta charset="utf-8">
<title>Lotusvale Spa – Ear Panel Advert</title>
<link rel="stylesheet" href="https://fonts.googleapis.com/css2?family=Montserrat:wght@400;600;700;800&display=swap">
<style>
  :root {
    --paper: #ffffff;
    --ink: #000000;
    --type: #ffffff;
    --band: #8c8c8c;
  }
  html, body {
    margin: 0;
    padding: 0;
    width: 1200px;
    height: 1200px;
    overflow: hidden;
    background: var(--paper);
  }
  .ad-canvas {
    display: block;
    width: 1200px;
    height: 1200px;
  }
  .ad-panel { fill: var(--ink); }
  .wave-band { fill: var(--band); }
  .ad-text {
    font-family: "Montserrat", Arial, sans-serif;
    fill: var(--type);
  }
  .brand-name { font-weight: 700; font-size: 128px; }
  .tagline { font-weight: 600; font-size: 31px; }
  .spa-word {
    font-weight: 400;
    font-size: 146px;
    fill: none;
    stroke: var(--type);
    stroke-width: 2.5;
  }
  .phone-number { font-weight: 700; font-size: 86px; }
  .web-address { font-weight: 700; font-size: 47px; }
  .phone-icon { fill: var(--type); }
</style>
</head>
<body>
<svg class="ad-canvas" viewBox="0 0 1200 1200" xmlns="http://www.w3.org/2000/svg">
  <rect class="ad-panel" x="102" y="284" width="994" height="626"/>

  <path class="wave-band wave-band--top" role="img" aria-label="Diagonal striped wave band"
        d="M102,284 L1096,284 L1096,332 C980,350 880,318 720,320 C560,322 430,352 300,345 C210,340 150,332 102,338 Z"/>
  <path class="wave-band wave-band--bottom" role="img" aria-label="Diagonal striped wave band"
        d="M102,862 C200,842 330,832 470,850 C610,868 760,862 880,845 C970,834 1040,850 1096,856 L1096,910 L102,910 Z"/>

  <text class="ad-text brand-name" x="182" y="472" textLength="836" lengthAdjust="spacingAndGlyphs">lotusvale</text>
  <text class="ad-text tagline" x="186" y="518" textLength="828" lengthAdjust="spacing">Balinese Massage Centre</text>
  <text class="ad-text spa-word" x="445" y="652" textLength="308" lengthAdjust="spacingAndGlyphs">SPA</text>

  <g class="phone-icon" transform="translate(238 700)">
    <path d="M4,18 C4,6 22,0 40,0 C58,0 76,6 76,18 L76,26 L58,26 L58,18 L22,18 L22,26 L4,26 Z"/>
    <path d="M16,30 L64,30 L74,62 L6,62 Z"/>
    <g fill="#000">
      <rect x="26" y="37" width="7" height="5"/><rect x="37" y="37" width="7" height="5"/><rect x="48" y="37" width="7" height="5"/>
      <rect x="24" y="45" width="7" height="5"/><rect x="37" y="45" width="7" height="5"/><rect x="50" y="45" width="7" height="5"/>
      <rect x="22" y="53" width="7" height="5"/><rect x="37" y="53" width="7" height="5"/><rect x="52" y="53" width="7" height="5"/>
    </g>
  </g>
  <text class="ad-text phone-number" x="338" y="760" textLength="628" lengthAdjust="spacingAndGlyphs">800 PIMBELO</text>

  <text class="ad-text web-address" x="246" y="826" textLength="724" lengthAdjust="spacing">www.lotusvale.ae</text>
</svg>
</body>
</html>
```